Community-based social network needs a new landing page

We need a landing page for a local social network in Singapore called "LaneKindred.sg". It is a website that help neighbours to connect with each other for mutual benefits such as providing professional/non-professional services, sharing items, and neighbourly help, etc.

There is an existing website but we want to completely revamp it. It is most important that the new landing page communicates that the neighbourhood has skills and services for people to discover.

The final design of the landing page should be modern, and communicates a sense of community and vibrancy. As a matter of priority, more real estate should be accorded to the neighbours providing services elements.

We have drafted 2 reference sites that communicates the key ideas/user propositions for your easy reference:
http://tarvelquin8.example-sites.com/lanekindred
http://tarvelquin8.example-sites.com/lanekindred2

As long as the key ideas/user propositions are kept to, we are open to any design proposals. I.e. you do not have to follow the design layout of the reference sites

Target Market(s)

Our target market is primarily the Singapore community, includes all genders, education levels and occupations, aged between 17-45 years old.

In the file uploaded, you will find pictures of Singapore neighbourhoods and people of local ethnicities. Please use them, but you may arrange and add further filters to better enhance them

Industry/Entity Type

Real Estate

Requirements
Nice to have
• Landing page could be similar to that of www.gatherloft.com, not just at the top, but also the way the other categories are presented at the bottom.

```html
<!DOCTYPE html>
<html lang="en">
<head>
<meta charset="utf-8">
<title>LaneKindred.sg</title>
<link href="https://fonts.googleapis.com/css2?family=Open+Sans:wght@300;400;600;700&display=swap" rel="stylesheet">
<style>
:root{
  --red:#d8232a;--navy:#163a68;--fb:#3b5ca0;--ink:#222;--muted:#8a8a8a;
  --sky1:#5aa9e6;--sky2:#bcdcf2;--water:#4d6f78;
  --coral:#f2846f;--lilac:#98a8db;--mint:#6fcfad;
  --panel:#f8f9fb;--grey:#ebebeb;--link:#3a9ac4;--foot:#454545;
  --lime:#d4eaa0;--pale:#a9b8e0;--teal:#2c8c9d;
}
*{margin:0;padding:0;box-sizing:border-box}
html,body{width:824px;height:1200px;overflow:hidden}
body{font-family:'Open Sans',sans-serif;color:var(--ink);position:relative;background:#fff}
.abs{position:absolute}
.topbar{left:0;top:0;width:824px;height:5px;background:var(--red)}
.brand{left:80px;top:34px;display:flex;align-items:center;gap:8px;font-size:24px;font-weight:700;color:var(--navy)}
.brand i{width:22px;height:22px;border-radius:50%;background:var(--red);display:block}
.btn{top:36px;height:22px;width:82px;font-size:12px;display:flex;align-items:center;justify-content:center;gap:8px}
.signup{left:475px;background:#e8e8e8;color:var(--ink)}
.login{left:568px;background:var(--navy);color:#fff}
.social-login{left:661px;background:var(--fb);color:#fff;border:1px solid #2c4a88}
.social-login b{width:8px;height:8px;background:#fff;display:block}
.city{left:0;top:86px;width:824px;height:880px;background:linear-gradient(180deg,var(--sky1) 0%,var(--sky2) 35%,#9fb7c6 58%,var(--water) 72%,#3c5a60 100%)}
.bubble{display:flex;font-size:8px;line-height:12px}
.bubble .face{background:linear-gradient(135deg,#8a6a55,#d9b59a);flex:none}
.bubble p{padding:9px 6px}
.dot{width:24px;height:24px;border-radius:50%;background:#d9d9d9;border:5px solid #9a9a9a}
.b1{left:69px;top:147px;width:208px;height:55px;background:var(--lime);border-bottom:2px solid #8aa060}
.b1 .face{width:55px}
.b2{left:516px;top:234px;width:226px;height:60px;background:var(--pale)}
.b2 .face{width:60px}
.b3{left:69px;top:308px;width:277px;height:73px;background:var(--teal);color:#fff}
.b3 .face{width:73px}
.panel{left:69px;top:418px;width:686px;height:548px;background:var(--panel)}
.headline{left:0;top:446px;width:824px;text-align:center;font-size:19px;font-weight:400}
.headline em{font-style:normal;font-weight:600;color:var(--red)}
.wave{left:83px;top:492px}
.service{top:532px;width:205px;height:176px;color:#fff;font-weight:300}
.service h3{position:absolute;left:52px;top:13px;font-size:14px;font-weight:400;line-height:14.5px}
.service svg{position:absolute;left:14px;top:12px}
.service p{position:absolute;left:14px;top:62px;width:180px;font-size:10px;line-height:16.5px}
.service .more{position:absolute;right:0;bottom:16px;width:55px;height:18px;background:rgba(255,255,255,.25);font-size:9px;display:flex;align-items:center;justify-content:center;font-family:Georgia,serif}
.s1{left:81px;background:var(--coral)}.s2{left:310px;background:var(--lilac)}.s3{left:538px;background:var(--mint)}
.strip{left:69px;top:754px;width:686px;height:212px;background:var(--grey)}
.strip-title{top:771px;font-size:11.5px;font-weight:600;color:var(--link)}
.member{width:45px;height:45px;background:linear-gradient(135deg,#c89e80,#6d5a50)}
.join{left:136px;top:918px;width:98px;height:31px;background:#111;color:#fff;font-size:14px;display:flex;align-items:center;justify-content:center}
.posts{left:328px;top:801px;list-style:none;font-size:8.5px;color:var(--muted)}
.posts li{height:21.6px;display:flex;align-items:center;gap:8px}
.posts li i{width:10px;height:9px;background:#aaa;border-radius:2px;display:block}
.feature{left:560px;width:183px}
.f1{top:797px;height:65px;background:linear-gradient(90deg,#3a2a1c,#f2ede6 40%,#e9f0e4 70%,#c8442c)}
.f2{top:878px;height:64px;background:linear-gradient(90deg,#e8c21a 0%,#1d4f9a 30%,#123e7c)}
.footer{left:0;top:966px;width:824px;height:234px;background:var(--foot);color:#fff}
.ftitle{font-size:11.5px;font-weight:600;color:#fff}
.widget{left:81px;top:1013px;width:333px;height:51px;background:#f3f3f3;border-radius:3px;font-size:7px;color:#333}
.count{width:36px;height:20px;background:#fff;border:1px solid #ccc;font-size:10px;display:flex;align-items:center;justify-content:center}
.mini{height:12px;background:#fff;border:1px solid #ccc;font-size:7px;padding:0 5px;display:flex;align-items:center;color:#555}
.media p{font-size:8.5px;line-height:14px;color:#aaa;font-weight:300}
.rule{left:69px;top:1094px;width:686px;height:1px;background:#555}
.col{top:1108px;font-size:8.5px;color:#aaa}
.col h4{font-size:11.5px;color:#fff;font-weight:600;margin-bottom:6px}
.col a{display:block;color:#bbb;font-weight:600;text-decoration:none;line-height:11.5px}
.col p{line-height:14px;font-weight:300}
</style>
</head>
<body>
<div class="abs topbar"></div>
<div class="abs brand"><i></i>LaneKindred.sg</div>
<div class="abs btn signup">Sign Up</div>
<div class="abs btn login">Login</div>
<div class="abs btn social-login"><b></b>Login</div>

<div class="abs city" role="img" aria-label="Singapore skyline of glass towers above the waterfront"></div>

<div class="abs bubble b1"><div class="face" role="img" aria-label="Portrait of a neighbour holding a guitar"></div><p>Aisha, a non-professional guitar enthusiast, will teach beginner guitar for only $5 per lesson</p></div>
<div class="abs dot" style="left:265px;top:190px"></div>
<div class="abs bubble b2"><div class="face" role="img" aria-label="Portrait of a young architecture student"></div><p>Mei Ling, an architecture under graduate, will design your home from only $200</p></div>
<div class="abs dot" style="left:730px;top:282px"></div>
<div class="abs bubble b3"><div class="face" role="img" aria-label="Portrait of a neighbour with her dog"></div><p>Aisha, a non-professional guitar enthusiast, will teach beginner guitar for only $5 per lesson</p></div>
<div class="abs dot" style="left:334px;top:368px"></div>

<div class="abs panel"></div>
<h1 class="abs headline">Find people living near you for <em>Useful</em> things &amp; <em>Neighbourly</em> help</h1>
<svg class="abs wave" width="660" height="6"><path d="M0 3 Q5 0 10 3 T20 3 T30 3 T40 3 T50 3 T60 3 T70 3 T80 3 T90 3 T100 3 T110 3 T120 3 T130 3 T140 3 T150 3 T160 3 T170 3 T180 3 T190 3 T200 3 T210 3 T220 3 T230 3 T240 3 T250 3 T260 3 T270 3 T280 3 T290 3 T300 3 T310 3 T320 3 T330 3 T340 3 T350 3 T360 3 T370 3 T380 3 T390 3 T400 3 T410 3 T420 3 T430 3 T440 3 T450 3 T460 3 T470 3 T480 3 T490 3 T500 3 T510 3 T520 3 T530 3 T540 3 T550 3 T560 3 T570 3 T580 3 T590 3 T600 3 T610 3 T620 3 T630 3 T640 3 T650 3 T660 3" fill="none" stroke="#ddd" stroke-width="1"/></svg>

<div class="abs service s1">
  <svg width="28" height="30" viewBox="0 0 28 30" fill="none" stroke="#fff" stroke-width="2"><circle cx="14" cy="11" r="9"/><path d="M9 6l10 10M19 6L9 16M7 18v10h10v-4"/></svg>
  <h3>Professional<br>Services</h3>
  <p>Maecenas non nunc libero, vitae imperdiet magna roin vulputate est vitae cursus urus vel turpis gravida semper roin vulputate.</p>
  <div class="more">More</div>
</div>
<div class="abs service s2">
  <svg width="36" height="30" viewBox="0 0 36 30" fill="#fff"><circle cx="26" cy="5" r="4"/><path d="M20 11h12v10h-4v8h-4v-8h-4z"/><path d="M2 2l16 13" stroke="#fff" stroke-width="2"/></svg>
  <h3 style="left:54px">Non Professional<br>Services</h3>
  <p>Proin elementum erat non velit hendrerit interdum pretium neque sag por interdum velit vel ultrici roin malesuada dui eget ipsum.</p>
  <div class="more">More</div>
</div>
<div class="abs service s3">
  <svg width="34" height="30" viewBox="0 0 34 30" fill="none" stroke="#fff" stroke-width="2"><ellipse cx="14" cy="11" rx="12" ry="9"/><path d="M8 19l-3 6 8-4M26 10c5 2 7 8 2 12l2 5-6-3"/></svg>
  <h3 style="left:56px">Non Professional<br>Services</h3>
  <p>Nam liber tempor cum soluta nobis eleifend option congue nihil imperdiet doming id quod mazim placerat facer possim assum.</p>
  <div class="more">More</div>
</div>

<div class="abs strip"></div>
<div class="abs strip-title" style="left:80px">Latest Members</div>
<div class="abs strip-title" style="left:328px">Latest Posts</div>
<div class="abs strip-title" style="left:560px">Latest Features</div>
<div class="abs member" style="left:81px;top:802px" role="img" aria-label="Member photo"></div>
<div class="abs member" style="left:133px;top:802px" role="img" aria-label="Member photo"></div>
<div class="abs member" style="left:183px;top:802px" role="img" aria-label="Member photo"></div>
<div class="abs member" style="left:235px;top:802px" role="img" aria-label="Member photo"></div>
<div class="abs member" style="left:81px;top:855px" role="img" aria-label="Member photo"></div>
<div class="abs member" style="left:133px;top:855px" role="img" aria-label="Member photo"></div>
<div class="abs member" style="left:183px;top:855px" role="img" aria-label="Member photo"></div>
<div class="abs member" style="left:235px;top:855px" role="img" aria-label="Member photo"></div>
<div class="abs join">Join for free</div>
<ul class="abs posts">
  <li><i></i>Ivy Seah has shared Measuring Tape</li>
  <li><i></i>Ivy Seah has shared Measuring Tape</li>
  <li><i></i>Ivy Seah has shared Novels</li>
  <li><i></i>Ivy Seah has shared Children Books</li>
  <li><i></i>Ivy Seah has shared Self Help Books</li>
  <li><i></i>Ivy Seah has shared Measuring Tape</li>
  <li><i></i>Ivy Seah has shared Novels</li>
</ul>
<div class="abs feature f1" role="img" aria-label="Feature banner for a health drink with fruit"></div>
<div class="abs feature f2" role="img" aria-label="Feature banner for a commerce software product"></div>

<div class="abs footer"></div>
<div class="abs ftitle" style="left:79px;top:989px">If you found LaneKindred.sg useful, tell your friends about it!</div>
<div class="abs widget">
  <div class="abs count" style="left:5px;top:5px">21</div>
  <div class="abs count" style="left:46px;top:5px">11</div>
  <div class="abs mini" style="left:90px;top:6px">Like</div>
  <div class="abs" style="left:125px;top:8px">516 people like this. Be the first of your friends.</div>
  <div class="abs mini" style="left:5px;top:31px">Post</div>
  <div class="abs mini" style="left:40px;top:31px">Share</div>
</div>
<div class="abs media" style="left:457px;top:989px;width:280px">
  <div class="ftitle" style="margin-bottom:3px">Media Mentions</div>
  <p>LaneKindred.sg is an initiative supported by CVRA.</p>
  <p style="margin-top:7px">“LaneKindred.sg fills a critical gap, by providing a mechanism for neighbours to communicate with each other their resources and their willingness to help.” - NMP Marcus Toh, CEO of CVRA</p>
</div>
<div class="abs rule"></div>
<div class="abs col" style="left:80px;width:250px"><h4>© Harrowfield Pte Ltd 2013</h4><p>LaneKindred.sg is a website of Harrowfield Pte Ltd. We help you pool together physical items, efforts, and purchasing power with your favourite neighbours so that you can save money, free up space at home, be eco-friendly.</p></div>
<div class="abs col" style="left:365px"><h4>Want to know more?</h4><a>About us</a><a>FAQ</a></div>
<div class="abs col" style="left:518px"><h4>Using LaneKindred</h4><a>Terms of Use</a><a>Privacy Policy</a></div>
<div class="abs col" style="left:676px"><h4>Get in touch</h4><a>Contact us</a><a>Social page</a></div>
</body>
</html>
```